VERDALIX " need somthing eye catching and envirnmental friendely materials

Business Card " UNIQUE..
- use the agreed on logo.
- use wooden background.
- the environmental sound should be HIGH.

Company slogan is ZERO DISCHARGE.
We work in deploying the latest technology “ USA & Europe” in the field of drill cutting recycle and economically managing the footprint.
With the ramp up in oil demands and the increase in oil prices , operators are extending their operations into new geographical areas “ government regulations and eco-sounds” created the need to a specialty services and products that should go parallel or even ahead.

Target Market(s)

OIL field and environmental concerned.
Mainly ENGINEERS.

Industry/Entity Type

Government

Font styles to use
Decorative
Script

Colors

Designer to choose colors to be used in the design.

Requirements
Must have
• Eco - sounded.

```html
<!DOCTYPE html>
<html lang="en">
<head>
<meta charset="utf-8">
<title>VERDALIX Business Card</title>
<link rel="stylesheet" href="https://fonts.googleapis.com/css2?family=Open+Sans:wght@400;600;700&display=swap">
<style>
  :root {
    --page-bg: #d9d6d0;
    --card-white: #f3f3f3;
    --ink-dark: #2b2b2b;
    --ink-mid: #555555;
    --ink-light: #9a9a9a;
    --eco-green: #5a9e3a;
    --oil-gold: #c89532;
    --plank-a: #1e1e1e;
    --plank-b: #262626;
    --plank-c: #2c2c2c;
    --plank-seam: #0d0d0d;
  }
  * { margin: 0; padding: 0; box-sizing: border-box; }
  html, body { width: 1200px; height: 900px; overflow: hidden; }
  body {
    background: var(--page-bg);
    font-family: "Open Sans", Arial, sans-serif;
    display: flex;
    flex-direction: column;
    align-items: center;
    justify-content: center;
    gap: 60px;
  }
  .card {
    width: 600px;
    height: 343px;
    position: relative;
    overflow: hidden;
    box-shadow: 0 6px 18px rgba(0,0,0,0.18);
  }

  /* Back side: dark wooden planks */
  .card-back { background: var(--plank-a); }
  .wood-planks {
    position: absolute; inset: 0;
    display: flex;
  }
  .plank {
    flex: 1;
    border-right: 2px solid var(--plank-seam);
    background: linear-gradient(180deg, var(--plank-b), var(--plank-a) 45%, var(--plank-b));
  }
  .plank:nth-child(3n+2) { background: linear-gradient(180deg, var(--plank-c), var(--plank-b) 60%, var(--plank-a)); }
  .plank:nth-child(3n) { background: linear-gradient(180deg, var(--plank-a), var(--plank-c) 50%, var(--plank-a)); }
  .plank:last-child { border-right: none; }
  .spot-light {
    position: absolute; inset: 0;
    background: radial-gradient(circle at 50% 50%, rgba(255,255,255,0.14) 0%, rgba(255,255,255,0) 45%, rgba(0,0,0,0.35) 100%);
  }
  .back-brand {
    position: absolute; inset: 0;
    display: flex; flex-direction: column; align-items: center; justify-content: center; gap: 10px;
  }
  .brand-line { display: flex; align-items: center; gap: 14px; }
  .brand-dot {
    width: 22px; height: 22px; border-radius: 50%;
    background: var(--eco-green);
  }
  .brand-name {
    font-weight: 700;
    font-size: 40px;
    letter-spacing: 3px;
    color: var(--eco-green);
    line-height: 1;
  }
  .brand-slogan {
    font-weight: 600;
    font-size: 12px;
    letter-spacing: 3px;
    color: var(--ink-light);
  }

  /* Front side */
  .card-front { background: var(--card-white); }
  .holder {
    position: absolute; left: 200px; top: 70px;
  }
  .holder-name {
    font-weight: 700; font-size: 17px; color: var(--ink-dark);
    letter-spacing: 0.5px;
  }
  .holder-role {
    font-size: 12px; color: var(--oil-gold); margin-top: 2px;
  }
  .contact-list {
    position: absolute; left: 176px; top: 132px;
    list-style: none;
  }
  .contact-item {
    display: flex; align-items: center; gap: 12px;
    font-size: 12px; color: var(--ink-mid);
    height: 22px;
  }
  .contact-icon { width: 12px; height: 12px; }
  .corner-disc {
    position: absolute;
    right: -150px; bottom: -190px;
    width: 400px; height: 400px;
    border-radius: 50%;
    background: linear-gradient(135deg, #d9a43a, var(--oil-gold) 50%, #6b4a1a);
  }
</style>
</head>
<body>
  <section class="card card-back">
    <div class="wood-planks">
      <span class="plank"></span><span class="plank"></span><span class="plank"></span>
      <span class="plank"></span><span class="plank"></span><span class="plank"></span>
      <span class="plank"></span><span class="plank"></span><span class="plank"></span>
      <span class="plank"></span>
    </div>
    <div class="spot-light"></div>
    <div class="back-brand">
      <div class="brand-line">
        <span class="brand-dot"></span>
        <span class="brand-name">VERDALIX</span>
      </div>
      <p class="brand-slogan">ZERO DISCHARGE · DRILLING SOLUTION</p>
    </div>
  </section>

  <section class="card card-front">
    <div class="holder">
      <p class="holder-name">KARIM NABIL HADDAD</p>
      <p class="holder-role">Chief Executive Officer</p>
    </div>
    <ul class="contact-list">
      <li class="contact-item">
        <svg class="contact-icon" viewBox="0 0 12 12"><rect x="3" y="1" width="6" height="10" rx="1" fill="none" stroke="var(--eco-green)" stroke-width="1.3"/></svg>
        <span>00971 5 312 480 26</span>
      </li>
      <li class="contact-item">
        <svg class="contact-icon" viewBox="0 0 12 12"><rect x="1" y="2.5" width="10" height="7" fill="none" stroke="var(--eco-green)" stroke-width="1.3"/><path d="M1 2.5 L6 6.5 L11 2.5" fill="none" stroke="var(--eco-green)" stroke-width="1.3"/></svg>
        <span>KH@VERDALIX.com</span>
      </li>
      <li class="contact-item">
        <svg class="contact-icon" viewBox="0 0 12 12"><circle cx="6" cy="6" r="4.6" fill="none" stroke="var(--eco-green)" stroke-width="1.3"/><path d="M1.4 6 H10.6 M6 1.4 V10.6" stroke="var(--eco-green)" stroke-width="1"/></svg>
        <span>www.VERDALIX.ae</span>
      </li>
    </ul>
    <div class="corner-disc"></div>
  </section>
</body>
</html>
```